Bold and Enticing Product Packaging - Dog Rolls (wet pet food)

Hello there and welcome to our project! Looking for fun and creative designs for our Dog Rolls (Wet Pet Food Rolls) sold at our butchery retail store.

We are a business located in Papua New Guinea and we manufacture and produce goods that we retail. Our target audience responds better to graphics/visual images rather than reading information - so keep it simple and attractive! Most animals here are working dogs (not leisure pets), so we must focus on this e.g. sell as ‘power for your dog’.

Looking for 2 x designs for each size (1kg & 3kg) – can be the same with different colour schemes/formats or similar. Require to be fully editable in both AI/PSD format.

Packaging dimensions are below. Designs will need to be repeated to fill 1m plastic casing. Note - more colours, more money, keep the colours to a minimum.
1kg product - 1 roll is 11cm wide (length of roll) and 25cm long (wrapped around). 1cm bleed.
3kg product - 1 roll is 16cm wide and 36cm long. 1cm bleed.

Information required (must have):
• 1kg or 3kg
• Real photo of a WORKING DOG (e.g. bullmastiff, doberman, rottweiler, german sheppard) and pet dog
• Brava Tuck logo & “power for your dog” combined... to read “Brava Tuck Power For Your Dog”.
• “Complete nutrition – for all dogs big or small”
• “Pet food only, not for human consumption. Keep refrigerated”

Would be cool (not a must-have) if we could include and be able to interchange the title of flavours (different products) e.g. Original Chunky.

Thank you and look forward to collaborating on some great designs here :)

Target Market(s)

See brief

Font styles to use
Sans Serif

Requirements
Must have
• See brief

```html
<!DOCTYPE html>
<html lang="en">
<head>
<meta charset="utf-8">
<title>Brava Tuck Dog Roll – 1kg Print Strip</title>
<link rel="stylesheet" href="https://fonts.googleapis.com/css2?family=Oswald:wght@400;500;600;700&display=swap">
<style>
  :root {
    --page: #e6e6e6;
    --casing-blue: #1f7fcf;
    --band-red: #c00000;
    --badge-red: #d0101e;
    --gold: #f7b500;
    --ink: #1a1a1a;
    --white: #ffffff;
    --dog-dark: #2a2c33;
    --dog-tan: #8a5a2b;
  }
  html, body {
    margin: 0;
    padding: 0;
    width: 1200px;
    height: 1151px;
    overflow: hidden;
    background: var(--page);
  }
  .canvas {
    position: relative;
    width: 1200px;
    height: 1151px;
    display: flex;
    align-items: center;
    justify-content: center;
  }
  .print-strip {
    height: 1111px;
    width: auto;
    display: block;
    box-shadow: 0 2px 10px rgba(0,0,0,.25);
  }
  .casing { fill: var(--casing-blue); }
  .cut-line { fill: none; stroke: var(--white); stroke-width: 1.5; stroke-dasharray: 10 8; opacity: .85; }
  .category-tag { fill: var(--gold); }
  .category-text { font-family: 'Oswald', sans-serif; font-weight: 600; font-size: 40px; fill: var(--ink); }
  .brand-name { font-family: 'Oswald', sans-serif; font-weight: 700; font-size: 58px; fill: var(--white); letter-spacing: 1px; }
  .tagline-band { fill: var(--band-red); }
  .tagline-text { font-family: 'Oswald', sans-serif; font-weight: 700; font-size: 34px; fill: var(--gold); }
  .flavour-box { fill: var(--white); }
  .flavour-text { font-family: 'Oswald', sans-serif; font-weight: 500; font-size: 44px; fill: var(--ink); }
  .notice-text { font-family: 'Oswald', sans-serif; font-weight: 400; font-size: 17px; fill: var(--white); }
  .paw { fill: var(--gold); }
  .weight-disc { fill: var(--gold); }
  .weight-num { font-family: 'Oswald', sans-serif; font-weight: 700; font-size: 32px; fill: var(--ink); }
  .weight-unit { font-family: 'Oswald', sans-serif; font-weight: 600; font-size: 16px; fill: var(--ink); }
  .nutrients-text { font-family: 'Oswald', sans-serif; font-weight: 400; font-style: italic; font-size: 18px; fill: #14223a; }
  .badge-dome { fill: var(--badge-red); stroke: var(--gold); stroke-width: 4; }
  .badge-bar { fill: var(--gold); }
  .badge-title { font-family: 'Oswald', sans-serif; font-weight: 700; font-size: 17px; fill: var(--white); }
  .badge-sub { font-family: 'Oswald', sans-serif; font-weight: 500; font-size: 12px; fill: var(--ink); }
  .dog-photo { fill: url(#dogTones); }
</style>
</head>
<body>
<main class="canvas">
  <svg class="print-strip" viewBox="0 0 812 1685" xmlns="http://www.w3.org/2000/svg">
    <defs>
      <linearGradient id="dogTones" x1="0" y1="0" x2="0" y2="1">
        <stop offset="0" stop-color="#2a2c33"/>
        <stop offset="0.6" stop-color="#33353d"/>
        <stop offset="1" stop-color="#6b4524"/>
      </linearGradient>
      <g id="paw-icon" class="paw">
        <ellipse cx="0" cy="4" rx="6" ry="4.5"/>
        <circle cx="-7" cy="-3" r="2.6"/>
        <circle cx="-2.5" cy="-6.5" r="2.6"/>
        <circle cx="2.5" cy="-6.5" r="2.6"/>
        <circle cx="7" cy="-3" r="2.6"/>
      </g>
      <g id="roll-panel">
        <rect class="dog-photo" x="410" y="85" width="380" height="475" rx="60" role="img" aria-label="Photo of a rottweiler working dog sitting, facing forward"/>

        <rect class="category-tag" x="170" y="116" width="176" height="51" rx="6"/>
        <text class="category-text" x="258" y="157" text-anchor="middle">DOG FOOD</text>

        <text class="brand-name" x="258" y="245" text-anchor="middle">BRAVA TUCK</text>

        <rect class="tagline-band" x="0" y="281" width="812" height="49"/>
        <text class="tagline-text" x="258" y="318" text-anchor="middle">POWER FOR YOUR DOG</text>

        <rect class="flavour-box" x="127" y="330" width="263" height="63" rx="5"/>
        <text class="flavour-text" x="258" y="379" text-anchor="middle">Original Chunky</text>

        <use href="#paw-icon" x="105" y="443"/>
        <use href="#paw-icon" x="105" y="470"/>
        <use href="#paw-icon" x="105" y="498"/>
        <text class="notice-text" x="122" y="450">PET FOOD ONLY,</text>
        <text class="notice-text" x="122" y="477">NOT FOR HUMAN CONSUMPTION.</text>
        <text class="notice-text" x="122" y="505">KEEP REFRIGERATED</text>

        <circle class="weight-disc" cx="430" cy="500" r="25"/>
        <text class="weight-num" x="424" y="512" text-anchor="middle">1</text>
        <text class="weight-unit" x="440" y="512" text-anchor="middle">kg</text>

        <text class="nutrients-text" x="76" y="553">*with added vitamins, minerals and other nutrients</text>

        <path class="badge-dome" d="M600 185 A48 48 0 0 1 696 185 Z"/>
        <text class="badge-title" x="648" y="162" text-anchor="middle">COMPLETE</text>
        <text class="badge-title" x="648" y="179" text-anchor="middle">NUTRITION</text>
        <rect class="badge-bar" x="588" y="189" width="120" height="26" rx="13"/>
        <text class="badge-sub" x="648" y="207" text-anchor="middle">for all dogs big or small</text>
      </g>
    </defs>

    <rect class="casing" x="0" y="0" width="812" height="1685"/>
    <rect class="cut-line" x="62" y="62" width="688" height="1563"/>

    <use href="#roll-panel" x="0" y="0"/>
    <use href="#roll-panel" x="0" y="522"/>
    <use href="#roll-panel" x="0" y="1044"/>
  </svg>
</main>
</body>
</html>
```